New Dental Office Needs an Attractive and user friendly Website Designed

I need a website for a new dental office. The Name is Harrowfield Dentistry. I would like a Modern design with a user friendly interface and usability.
I would like a landing page, a page that lists the services we offer: Cosmetic Dentistry, Implants, Dental Hygiene, Emergency Services, Restorations, Dentures
Target Market(s)
Mid to upper class
Industry/Entity Type
Dentistry
Coding
Number of Pages Required
1 page
Requirements
Must have
- Landing page that has a scheduling option, Procedures, operating hours, and contact us info
Nice to have
- Appealing design, Soft comforting colors. Easy to navigate page, Modern and professional.

```html
<!DOCTYPE html>
<html lang="en">
<head>
<meta charset="utf-8">
<title>Harrowfield Dentistry</title>
<link href="https://fonts.googleapis.com/css2?family=Prata&family=Montserrat:wght@400;500;600;700&display=swap" rel="stylesheet">
<style>
:root{
  --cyan:#1fa9ea;
  --navy:#0a47a0;
  --navy-deep:#083c8a;
  --ice:#e4f4fc;
  --ice-2:#d2ecf8;
  --ink:#1b1b1b;
  --muted:#555;
  --footer:#0c0c0c;
  --white:#fff;
}
*{margin:0;padding:0;box-sizing:border-box}
html,body{width:1200px;height:4789px;overflow:hidden}
body{font-family:"Montserrat",sans-serif;color:var(--ink);background:var(--white);position:relative}
.serif{font-family:"Prata",serif;font-weight:400}
.abs{position:absolute}
.btn{position:absolute;display:flex;align-items:center;justify-content:center;gap:8px;background:var(--cyan);color:#fff;border-radius:40px;font-size:12px;font-weight:600;letter-spacing:.3px;text-transform:uppercase}
.btn svg{width:14px;height:14px}
.logo{position:absolute;text-align:center;line-height:1}
.logo .name{font-family:"Prata",serif;font-size:34px}
.logo .sub{font-size:13px;letter-spacing:5px;font-weight:600;margin-top:4px}

/* header */
.site-header{position:absolute;left:0;top:0;width:1200px;height:90px;background:#fff}
.nav a{position:absolute;top:36px;font-size:12px;font-weight:600;color:var(--ink);text-decoration:none}
.nav a.active{color:var(--cyan)}

/* hero */
.hero{position:absolute;left:0;top:90px;width:1200px;height:533px;background:linear-gradient(110deg,#e9f6fc 0%,#d6eef9 60%,#cfe8f4 100%);overflow:hidden}
.hero-photo{position:absolute;left:650px;top:0;width:550px;height:533px;background:linear-gradient(180deg,#dceef6,#c9e2ee)}
.hero-prop{position:absolute;left:0;top:300px;width:170px;height:233px;background:linear-gradient(160deg,#f2f8fb,#d7e9f2);border-radius:0 90px 0 0}
.hero h1{position:absolute;left:141px;top:96px;font-size:51px;line-height:63px}
.hero p{position:absolute;left:141px;top:300px;font-size:21px;line-height:32px}
.chat-card{position:absolute;left:825px;top:421px;width:200px;height:56px;background:#fff;border-radius:30px;box-shadow:0 4px 14px rgba(0,0,0,.1);font-size:10px;display:flex;align-items:center;padding-left:48px;line-height:13px}
.chat-card .av{position:absolute;left:14px;top:14px;width:28px;height:28px;border-radius:50%;background:#b9cbd5}
.chat-btn{position:absolute;left:1010px;top:417px;width:64px;height:64px;border-radius:50%;background:var(--navy);border:5px solid #cfe6f3;display:flex;align-items:center;justify-content:center}
.chat-x{position:absolute;left:822px;top:420px;width:18px;height:18px;border-radius:50%;background:#111;color:#fff;font-size:11px;display:flex;align-items:center;justify-content:center;font-weight:700}

/* about */
.about-img{position:absolute;left:141px;top:708px;width:428px;height:428px;border-radius:50%;background:linear-gradient(135deg,#e7eef3,#9eb6c9 60%,#2f5da0)}
.video{position:absolute;left:418px;top:1013px;width:168px;height:168px;border-radius:50%;background:linear-gradient(135deg,#3d7ac1,#1a4d96);border:6px solid #fff;display:flex;align-items:center;justify-content:center}
.about h2{position:absolute;left:658px;top:727px;font-size:33px}
.about .kicker{position:absolute;left:658px;top:778px;font-size:12px;letter-spacing:3.5px;font-weight:600}
.about .copy{position:absolute;left:658px;top:808px;width:404px;font-size:12.5px;line-height:22px;color:#333}
.about .copy p+p{margin-top:12px}
.callus{position:absolute;display:flex;align-items:center;gap:12px;font-size:13px;font-weight:600;line-height:17px}
.callus .ic{width:40px;height:40px;border-radius:50%;background:var(--navy);display:flex;align-items:center;justify-content:center;border:4px solid #d9ebf7}
.callus .ic svg{width:16px;height:16px}

/* info band */
.info{position:absolute;left:0;top:1282px;width:1200px;height:545px}
.doc-photo{position:absolute;left:0;top:0;width:498px;height:545px;background:linear-gradient(180deg,#f2f3f4,#e2e5e8)}
.doc-call{position:absolute;left:160px;top:474px;width:172px;height:42px;border-radius:30px;background:var(--cyan);color:#fff;display:flex;align-items:center;gap:10px;padding-left:6px;font-size:13px;font-weight:600;line-height:15px}
.doc-call small{font-size:10px;font-weight:500}
.doc-call .ic{width:32px;height:32px;border-radius:50%;background:var(--navy);display:flex;align-items:center;justify-content:center}
.hours{position:absolute;left:498px;top:0;width:279px;height:545px;background:var(--ice)}
.hours h3{position:absolute;left:36px;top:40px;font-size:18px}
.hours .row{position:absolute;left:36px;font-size:12px;display:flex}
.hours .row span:first-child{width:88px;font-weight:500}
.hours .row small{display:block;font-size:11px;margin-top:6px}
.where{position:absolute;left:777px;top:0;width:423px;height:545px;background:var(--navy);color:#fff}
.where h3{position:absolute;left:33px;top:40px;font-size:18px}
.where .t{position:absolute;font-size:12px;line-height:17px}
.where hr{position:absolute;left:33px;width:360px;border:0;border-top:1px solid rgba(255,255,255,.25)}
.field{position:absolute;height:40px;width:160px;background:#fff;border-radius:20px;color:#555;font-size:11px;padding-left:16px;display:flex;align-items:center}
.chk{display:inline-block;width:13px;height:13px;border:1px solid #9db8e2;border-radius:2px;vertical-align:middle;margin-right:4px}

/* services */
.services h2{position:absolute;top:1910px;width:1200px;text-align:center;font-size:34px}
.card{position:absolute;width:288px;height:426px;border-bottom:4px solid var(--navy)}
.card.featured{background:#f1f1f1;border-bottom-color:var(--cyan)}
.card .ph{height:203px;width:100%}
.card .badge{position:absolute;left:108px;top:168px;width:72px;height:72px;border-radius:50%;background:var(--navy);border:4px solid #fff;display:flex;align-items:center;justify-content:center}
.card h3{position:absolute;top:250px;width:100%;text-align:center;font-size:21px;font-weight:500}
.card p{position:absolute;top:286px;left:20px;right:20px;text-align:center;font-size:14.5px;line-height:24px;color:#444}
.card .btn{left:71px;top:352px;width:146px;height:41px}
.card.featured .btn{background:var(--navy)}

/* why */
.why{position:absolute;left:0;top:2989px;width:1200px;height:627px;background:var(--ice)}
.why h2{position:absolute;left:144px;top:78px;font-size:34px}
.feat{position:absolute;top:165px;width:170px;z-index:1}
.feat .ic{width:60px;height:60px;border-radius:50%;background:#fff;display:flex;align-items:center;justify-content:center}
.feat h4{font-family:"Prata",serif;font-weight:400;font-size:15px;line-height:20px;margin-top:24px}
.feat p{font-size:12px;line-height:19px;color:#444;margin-top:18px}
.feat .more{font-size:11px;font-weight:600;margin-top:16px;display:flex;align-items:center;gap:8px}
.feat .more i{width:14px;height:14px;border-radius:50%;background:#111;display:inline-block}
.why-call{position:absolute;left:138px;top:483px;width:172px;height:46px;border-radius:30px;background:#fff;display:flex;align-items:center;gap:10px;padding-left:4px;font-size:13px;font-weight:600;line-height:15px}
.why-call small{font-size:10px;font-weight:500}
.why-call .ic{width:38px;height:38px;border-radius:50%;background:var(--navy);display:flex;align-items:center;justify-content:center;border:3px solid #d9ebf7}
.tooth-art{position:absolute;left:940px;top:410px;width:190px;height:150px;z-index:0;border-radius:60px 60px 40px 40px;background:linear-gradient(160deg,#f7f9fb,#d3dde4)}

/* reviews */
.rating{position:absolute;left:141px;top:3740px;width:180px;text-align:center}
.rating .big{font-size:26px;font-weight:500}
.stars{color:#f6a51a;font-size:28px;letter-spacing:4px}
.rating .based{font-size:13px;margin-top:4px}
.rating .plats{display:flex;justify-content:center;gap:12px;margin-top:16px}
.rating .plats span{width:36px;height:36px;border:1px solid #ddd;background:#fff}
.rev{position:absolute;top:3709px;width:294px;height:232px;background:#fff;box-shadow:0 4px 20px rgba(0,0,0,.08);padding:24px 30px}
.rev .s{color:#f6a51a;font-size:15px;letter-spacing:3px}
.rev .g{position:absolute;right:30px;top:24px;width:20px;height:20px;border-radius:50%;background:#e3e3e3}
.rev p{font-size:12px;line-height:21px;color:#444;margin-top:12px}
.rev h5{font-size:16px;font-weight:600;margin-top:28px}
.arrow-l{position:absolute;left:345px;top:3802px;width:44px;height:44px;border-radius:50%;background:var(--cyan);color:#fff;display:flex;align-items:center;justify-content:center;font-size:18px}

/* cta */
.footer{position:absolute;left:0;top:4285px;width:1200px;height:504px;background:var(--footer);color:#fff}
.cta{position:absolute;left:204px;top:4080px;width:792px;height:298px;background:linear-gradient(120deg,#f0f8fc,#d4ebf6);border-radius:16px;text-align:center}
.cta .hand-l{position:absolute;left:40px;top:175px;width:200px;height:90px;background:linear-gradient(90deg,#4db3e6,#bfe3f4);border-radius:45px;opacity:.85}
.cta .hand-r{position:absolute;right:0;top:50px;width:200px;height:130px;background:linear-gradient(90deg,#bfe3f4,#4db3e6);border-radius:65px 16px 16px 65px;opacity:.85}
.cta h2{position:absolute;top:72px;width:100%;font-size:34px}
.cta h3{position:absolute;top:122px;width:100%;font-size:22px}
.cta p{position:absolute;top:162px;width:100%;font-size:12.5px;line-height:21px;color:#333}
.leaf{position:absolute;left:555px;top:4026px;width:90px;height:90px;border-radius:50%;background:#fff;box-shadow:0 4px 14px rgba(0,0,0,.08);display:flex;align-items:center;justify-content:center}
.footer h4{position:absolute;font-family:"Prata",serif;font-weight:400;font-size:17px}
.footer ul{position:absolute;list-style:none;font-size:12.5px;line-height:30.5px}
.vline{position:absolute;top:165px;width:1px;height:250px;background:rgba(255,255,255,.18)}
.socials{position:absolute;left:141px;top:338px;display:flex;gap:14px}
.socials span{width:30px;height:30px;border-radius:50%;background:#fff}
.socials span.on{background:var(--cyan)}
.sub-form{position:absolute;left:450px;top:331px;width:292px;height:38px;border:1px solid #444;border-radius:20px;font-size:11px;display:flex;align-items:center;padding-left:18px}
.sub-form b{position:absolute;right:-2px;top:-1px;height:38px;width:92px;border-radius:20px;background:var(--cyan);display:flex;align-items:center;justify-content:center;font-size:11px;font-weight:600}
.copyright{position:absolute;top:466px;width:1200px;text-align:center;font-size:12px}
.fdiv{position:absolute;left:141px;top:440px;width:918px;border-top:1px solid rgba(255,255,255,.15)}
</style>
</head>
<body>

<!-- header -->
<header class="site-header">
  <div class="logo" style="left:130px;top:14px"><div class="name">Harrowfield</div><div class="sub">— DENTISTRY —</div></div>
  <nav class="nav">
    <a class="active" style="left:510px">HOME</a>
    <a style="left:593px">SERVICES</a>
    <a style="left:700px">CONTACT US</a>
  </nav>
  <div class="btn" style="left:827px;top:24px;width:231px;height:41px">
    <svg viewBox="0 0 16 16" fill="none" stroke="#fff" stroke-width="1.5"><rect x="2" y="3" width="12" height="11" rx="1"/><path d="M2 6h12M5 1v4M11 1v4"/></svg>Book an appointment
  </div>
</header>

<!-- hero -->
<section class="hero">
  <div class="hero-prop" role="img" aria-label="Dental mirror resting against a white tooth model"></div>
  <div class="hero-photo" role="img" aria-label="Smiling young woman touching her cheek"></div>
  <h1 class="serif">Premium Dental<br>Care for a Confident<br>Smile</h1>
  <p>Expert Cosmetic And Restorative Dentistry<br>In A Luxurious Setting.</p>
  <div class="btn" style="left:141px;top:386px;width:233px;height:41px">
    <svg viewBox="0 0 16 16" fill="none" stroke="#fff" stroke-width="1.5"><rect x="2" y="3" width="12" height="11" rx="1"/><path d="M2 6h12M5 1v4M11 1v4"/></svg>Book an appointment
  </div>
  <div class="chat-card"><span class="av" role="img" aria-label="Support agent avatar"></span>Lorem Ipsum Simply<br>Dummy Text.</div>
  <div class="chat-x">×</div>
  <div class="chat-btn"><svg width="26" height="26" viewBox="0 0 24 24"><path d="M12 3C6.5 3 3 6.6 3 11c0 2.3 1 4.3 2.7 5.7L5 21l4.2-2.2c.9.2 1.8.3 2.8.3 5.5 0 9-3.6 9-8s-3.5-8-9-8z" fill="#fff"/><circle cx="8" cy="11" r="1.2" fill="#0a47a0"/><circle cx="12" cy="11" r="1.2" fill="#0a47a0"/><circle cx="16" cy="11" r="1.2" fill="#0a47a0"/></svg></div>
</section>

<!-- about -->
<section class="about">
  <div class="about-img" role="img" aria-label="Modern dental treatment chair in a bright clinic room"></div>
  <div class="video" role="img" aria-label="Video preview of the dental team"><svg width="30" height="30" viewBox="0 0 24 24"><path d="M7 4l13 8-13 8z" fill="#fff"/></svg></div>
  <h2 class="serif">About Harrowfield</h2>
  <div class="kicker">DENTISTRY—</div>
  <div class="copy">
    <p>Lorem ipsum dolor sit amet, consectetuer adipiscing elit, sed diam nonummy nibh euismod tincidunt ut laoreet dolore magna aliquam erat volutpat. Ut wisi enim ad minim veniam, quis nostrud exerci tation ullamcorper suscipit lobortis nisl ut aliquip ex ea commodo consequat.</p>
    <p>Duis autem vel eum iriure dolor in hendrerit in vulputate velit esse molestie consequat, vel illum dolore eu feugiat nulla facilisis at vero eros et accumsan et iusto odio dignissim qui blandit praesent luptatum zzril delenit augue duis dolore te feugait nulla facilisi.</p>
  </div>
  <div class="btn" style="left:657px;top:1067px;width:226px;height:41px">
    <svg viewBox="0 0 16 16" fill="none" stroke="#fff" stroke-width="1.5"><rect x="2" y="3" width="12" height="11" rx="1"/><path d="M2 6h12M5 1v4M11 1v4"/></svg>Book an appointment
  </div>
  <div class="callus" style="left:902px;top:1066px">
    <span class="ic"><svg viewBox="0 0 24 24"><path d="M6.6 10.8a15 15 0 006.6 6.6l2.2-2.2c.3-.3.7-.4 1-.2 1.1.4 2.3.6 3.6.6.6 0 1 .4 1 1V20c0 .6-.4 1-1 1A17 17 0 013 4c0-.6.4-1 1-1h3.5c.6 0 1 .4 1 1 0 1.3.2 2.5.6 3.6.1.3 0 .7-.2 1z" fill="#fff"/></svg></span>
    <span>CALL US<br>123 456 7890</span>
  </div>
</section>

<!-- hours & contact -->
<section class="info">
  <div class="doc-photo" role="img" aria-label="Smiling dentist in white uniform with arms crossed"></div>
  <div class="doc-call">
    <span class="ic"><svg width="14" height="14" viewBox="0 0 24 24"><path d="M6.6 10.8a15 15 0 006.6 6.6l2.2-2.2c.3-.3.7-.4 1-.2 1.1.4 2.3.6 3.6.6.6 0 1 .4 1 1V20c0 .6-.4 1-1 1A17 17 0 013 4c0-.6.4-1 1-1h3.5c.6 0 1 .4 1 1 0 1.3.2 2.5.6 3.6.1.3 0 .7-.2 1z" fill="#fff"/></svg></span>
    <span><small>CALL US</small><br>123 456 7890</span>
  </div>
  <div class="hours">
    <h3 class="serif">Opening Hours</h3>
    <div class="row" style="top:100px"><span>Monday</span><span>9.00am - 8.00pm</span></div>
    <div class="row" style="top:156px"><span>Tuesday</span><span>9.00am - 8.00pm</span></div>
    <div class="row" style="top:214px"><span>Wednesday</span><span>9.00am - 8.00pm</span></div>
    <div class="row" style="top:270px"><span>Thursday</span><span>9.00am - 8.00pm</span></div>
    <div class="row" style="top:326px"><span>Friday</span><span>9.00am - 8.00pm</span></div>
    <div class="row" style="top:383px"><span>Saturday</span><span>9.00am - 8.00pm</span></div>
    <div class="row" style="top:441px"><span>Sunday</span><span>Closed<small>(By Appointment Only)</small></span></div>
  </div>
  <div class="where">
    <h3 class="serif">Where Are We?</h3>
    <div class="t" style="left:35px;top:72px">Come visit us today in USA</div>
    <svg class="abs" style="left:33px;top:104px" width="14" height="16" viewBox="0 0 24 24"><path d="M12 2a7 7 0 00-7 7c0 5 7 13 7 13s7-8 7-13a7 7 0 00-7-7zm0 9.5A2.5 2.5 0 1112 6a2.5 2.5 0 010 5.5z" fill="#5cc3f2"/></svg>
    <div class="t" style="left:60px;top:104px">Address: 123 Ut wisi enim minim<br>veniam, quis nostrud tation.</div>
    <hr style="top:152px">
    <svg class="abs" style="left:33px;top:174px" width="14" height="14" viewBox="0 0 24 24"><path d="M6.6 10.8a15 15 0 006.6 6.6l2.2-2.2c.3-.3.7-.4 1-.2 1.1.4 2.3.6 3.6.6.6 0 1 .4 1 1V20c0 .6-.4 1-1 1A17 17 0 013 4c0-.6.4-1 1-1h3.5c.6 0 1 .4 1 1 0 1.3.2 2.5.6 3.6.1.3 0 .7-.2 1z" fill="#5cc3f2"/></svg>
    <div class="t" style="left:58px;top:173px">123 456 7890</div>
    <svg class="abs" style="left:162px;top:176px" width="15" height="11" viewBox="0 0 20 14" fill="none" stroke="#5cc3f2" stroke-width="1.6"><rect x="1" y="1" width="18" height="12"/><path d="M1 1l9 7 9-7"/></svg>
    <div class="t" style="left:190px;top:173px">info@harrowfielddental.com</div>
    <hr style="top:216px">
    <svg class="abs" style="left:33px;top:244px" width="22" height="22" viewBox="0 0 16 16" fill="none" stroke="#fff" stroke-width="1.3"><rect x="2" y="3" width="12" height="11" rx="1"/><path d="M2 6h12M5 1v4M11 1v4M5 9h1M8 9h1M11 9h1M5 11.5h1M8 11.5h1"/></svg>
    <div class="t serif" style="left:70px;top:244px;font-size:17px">Book an Appointment</div>
    <div class="field" style="left:27px;top:290px">Full Name</div>
    <div class="field" style="left:203px;top:290px">Phone Number</div>
    <div class="field" style="left:27px;top:344px">Email Address</div>
    <div class="field" style="left:203px;top:344px">mm/dd/yyyy</div>
    <div class="btn" style="left:27px;top:403px;width:234px;height:40px">
      <svg viewBox="0 0 16 16" fill="none" stroke="#fff" stroke-width="1.5"><rect x="2" y="3" width="12" height="11" rx="1"/><path d="M2 6h12M5 1v4M11 1v4"/></svg>Book an appointment
    </div>
    <div class="t" style="left:40px;top:468px;font-size:10.5px"><span class="chk"></span>Yes &nbsp; <span class="chk"></span>No &nbsp;&nbsp;&nbsp; Have you visited us before?</div>
  </div>
</section>

<!-- services -->
<section class="services">
  <h2 class="serif">Our Services</h2>

  <article class="card" style="left:141px;top:1981px">
    <div class="ph" role="img" aria-label="Woman smiling in a dental chair during a cosmetic exam" style="background:linear-gradient(135deg,#5d7d98,#c5a49a)"></div>
    <div class="badge"><svg width="32" height="32" viewBox="0 0 24 24" fill="none" stroke="#fff" stroke-width="1.4"><path d="M7 3c-2.5 0-4 2-4 4.5 0 3 1.5 4.5 2 7 .5 3 1 6.5 2.5 6.5S9.5 16 12 16s3 5 4.5 5 2-3.5 2.5-6.5c.5-2.5 2-4 2-7C21 5 19.5 3 17 3c-2 0-3 1-5 1S9 3 7 3z"/></svg></div>
    <h3>Cosmetic Dentistry</h3>
    <p>Ut wisi enim ad minim veniam quis nostrud exerci tat ulla.</p>
    <div class="btn">Read more</div>
  </article>

  <article class="card featured" style="left:457px;top:1981px">
    <div class="ph" role="img" aria-label="Dentist holding a dental implant model" style="background:linear-gradient(135deg,#8e9aa3,#3a3f45)"></div>
    <div class="badge" style="background:var(--cyan)"><svg width="32" height="32" viewBox="0 0 24 24" fill="none" stroke="#fff" stroke-width="1.4"><path d="M6 3h12v4c0 2-2 3-6 3S6 9 6 7z"/><path d="M9 10v2h6v-2M9 14h6M10 16h4M11 18h2v3h-2z"/></svg></div>
    <h3>Implants</h3>
    <p>Ut wisi enim ad minim veniam quis nostrud exerci tat ulla.</p>
    <div class="btn">Read more</div>
  </article>

  <article class="card" style="left:773px;top:1981px">
    <div class="ph" role="img" aria-label="Woman brushing her teeth" style="background:linear-gradient(135deg,#efe6dc,#b99a82)"></div>
    <div class="badge"><svg width="32" height="32" viewBox="0 0 24 24" fill="none" stroke="#fff" stroke-width="1.4"><path d="M3 5h14v3H3zM5 8v2M8 8v2M11 8v2M14 8v2"/><path d="M7 13c-2 0-3 1.5-3 3 0 2 1 3 1.5 5M17 13c2 0 3 1.5 3 3 0 2-1 3-1.5 5M7 13c2 0 3 1 5 1s3-1 5-1"/></svg></div>
    <h3>Dental Hygiene</h3>
    <p>Ut wisi enim ad minim veniam quis nostrud exerci tat ulla.</p>
    <div class="btn">Read more</div>
  </article>

  <article class="card" style="left:141px;top:2448px">
    <div class="ph" role="img" aria-label="Gloved hands holding a tooth restoration model" style="background:linear-gradient(135deg,#c8bfa2,#d1634a)"></div>
    <div class="badge"><svg width="32" height="32" viewBox="0 0 24 24" fill="none" stroke="#fff" stroke-width="1.4"><path d="M7 3c-2.5 0-4 2-4 4.5 0 3 1.5 4.5 2 7 .5 3 1 6.5 2.5 6.5S9.5 16 12 16s3 5 4.5 5 2-3.5 2.5-6.5c.5-2.5 2-4 2-7C21 5 19.5 3 17 3c-2 0-3 1-5 1S9 3 7 3z"/><path d="M9 8l2 3 2-3 2 3"/></svg></div>
    <h3>Restorations</h3>
    <p>Ut wisi enim ad minim veniam quis nostrud exerci tat ulla.</p>
    <div class="btn">Read more</div>
  </article>

  <article class="card" style="left:457px;top:2448px">
    <div class="ph" role="img" aria-label="Dentist showing a denture model to a patient" style="background:linear-gradient(135deg,#dcd8d3,#c87780)"></div>
    <div class="badge"><svg width="32" height="32" viewBox="0 0 24 24" fill="none" stroke="#fff" stroke-width="1.4"><rect x="3" y="6" width="18" height="12" rx="5"/><path d="M6 12h12M8 9v6M11 9v6M14 9v6M17 9v6"/></svg></div>
    <h3>Dentures</h3>
    <p>Ut wisi enim ad minim veniam quis nostrud exerci tat ulla.</p>
    <div class="btn">Read more</div>
  </article>

  <article class="card" style="left:773px;top:2448px">
    <div class="ph" role="img" aria-label="Dentist treating a patient in an emergency visit" style="background:linear-gradient(135deg,#2c5a9a,#7fa4c9)"></div>
    <div class="badge"><svg width="32" height="32" viewBox="0 0 24 24" fill="none" stroke="#fff" stroke-width="1.4"><path d="M12 21s-8-5-8-11a4 4 0 018-1 4 4 0 018 1c0 6-8 11-8 11z"/><path d="M12 9v6M9 12h6"/></svg></div>
    <h3>Emergency Services</h3>
    <p>Ut wisi enim ad minim veniam quis nostrud exerci tat ulla.</p>
    <div class="btn">Read more</div>
  </article>
</section>

<!-- why choose us -->
<section class="why">
  <h2 class="serif">Why Choose Us</h2>
  <div class="tooth-art" role="img" aria-label="White tooth model with dental mirror and implant"></div>
  <div class="feat" style="left:141px">
    <div class="ic"><svg width="28" height="28" viewBox="0 0 24 24" fill="none" stroke="#1fa9ea" stroke-width="1.4"><rect x="3" y="4" width="18" height="14" rx="1"/><circle cx="12" cy="10" r="3"/><path d="M10 13l-1 5 3-1.5 3 1.5-1-5"/></svg></div>
    <h4>Board-Certified<br>Dentists</h4>
    <p>Ut wisi enim ad minim veniam quis nostrud exerci tat ulla.</p>
    <div class="more">READ MORE <i></i></div>
  </div>
  <div class="feat" style="left:375px">
    <div class="ic"><svg width="28" height="28" viewBox="0 0 24 24" fill="none" stroke="#1fa9ea" stroke-width="1.4"><rect x="4" y="4" width="12" height="17" rx="1"/><path d="M7 3h6v3H7zM7 10h6M7 13h4"/><circle cx="17" cy="16" r="4"/><path d="M15.5 16l1 1 2-2"/></svg></div>
    <h4>Pain-Free<br>Treatments</h4>
    <p>Ut wisi enim ad minim veniam quis nostrud exerci tat ulla.</p>
    <div class="more">READ MORE <i></i></div>
  </div>
  <div class="feat" style="left:598px">
    <div class="ic"><svg width="28" height="28" viewBox="0 0 24 24" fill="none" stroke="#1fa9ea" stroke-width="1.4"><path d="M5 19l5-5M4 20l2 0M14 5c3 0 5 2 5 5 0 2-1 3-1 5s-1 4-2 4-1.5-3-3-3-2 3-3 3"/><path d="M8 6l3 3"/></svg></div>
    <h4>Luxury,<br>Comfort-First Clinic</h4>
    <p>Ut wisi enim ad minim veniam quis nostrud exerci tat ulla.</p>
    <div class="more">READ MORE <i></i></div>
  </div>
  <div class="feat" style="left:816px">
    <div class="ic"><svg width="28" height="28" viewBox="0 0 24 24" fill="none" stroke="#1fa9ea" stroke-width="1.4"><rect x="3" y="6" width="16" height="11" rx="1"/><path d="M3 9h16M6 14h4M6 4h15v11"/></svg></div>
    <h4>Flexible Payment<br>Plans</h4>
    <p>Ut wisi enim ad minim veniam quis nostrud exerci tat ulla.</p>
    <div class="more">READ MORE <i></i></div>
  </div>
  <div class="why-call">
    <span class="ic"><svg width="14" height="14" viewBox="0 0 24 24"><path d="M6.6 10.8a15 15 0 006.6 6.6l2.2-2.2c.3-.3.7-.4 1-.2 1.1.4 2.3.6 3.6.6.6 0 1 .4 1 1V20c0 .6-.4 1-1 1A17 17 0 013 4c0-.6.4-1 1-1h3.5c.6 0 1 .4 1 1 0 1.3.2 2.5.6 3.6.1.3 0 .7-.2 1z" fill="#fff"/></svg></span>
    <span><small>CALL US</small><br>123 456 7890</span>
  </div>
</section>

<!-- reviews -->
<section class="reviews">
  <div class="rating">
    <div class="big">4.8 Stars</div>
    <div class="stars">★★★★★</div>
    <div class="based">Based on <u>267 reviews</u></div>
    <div class="plats"><span></span><span></span><span></span></div>
  </div>
  <div class="arrow-l">«</div>
  <div class="rev" style="left:368px">
    <div class="s">★★★★★</div><span class="g"></span>
    <p>Lorem Ipsum is simply dummy text of the printing and typesett industry. Lorem Ipsum has been the industrys standard dummy text ever since the 1500s, when an unknown.</p>
    <h5>Nadia Brookes</h5>
  </div>
  <div class="rev" style="left:673px">
    <div class="s">★★★★★</div><span class="g"></span>
    <p>Lorem Ipsum is simply dummy text of the printing and typesett industry. Lorem Ipsum has been the industrys standard dummy text ever since the 1500s, when an unknown.</p>
    <h5>Carla Wenlow</h5>
  </div>
  <div class="rev" style="left:980px;width:260px">
    <div class="s">★★★★★</div>
    <p>Lorem Ipsum is simply dummy text of the printing and typesett in Lorem Ipsum has been the ind standard dummy text ever sin 1500s, when an unknown.</p>
    <h5>Jodie</h5>
  </div>
</section>

<!-- footer -->
<footer class="footer">
  <h4 style="left:141px;top:167px">Quick Links</h4>
  <ul style="left:143px;top:198px"><li>Home</li><li>Services</li><li>Contact Us</li></ul>
  <div class="socials"><span></span><span class="on"></span><span></span><span></span></div>
  <div class="vline" style="left:387px"></div>
  <div class="logo" style="left:472px;top:168px;width:256px"><div class="name">Harrowfield</div><div class="sub">— DENTISTRY —</div></div>
  <p class="abs" style="left:440px;top:248px;width:320px;text-align:center;font-size:13.5px;line-height:21px">Enter your email to receive the latest news about our opening. events, special offers and more.</p>
  <div class="sub-form">Your Email<b>SIGN UP</b></div>
  <div class="vline" style="left:812px"></div>
  <h4 style="left:881px;top:167px">Our Services</h4>
  <ul style="left:881px;top:198px"><li>Cosmetic Dentistry</li><li>Implants</li><li>Dental Hygiene</li><li>Restorations</li><li>Dentures</li><li>Emergency Services</li></ul>
  <div class="fdiv"></div>
  <div class="copyright">© 2025 Harrowfield. All Rights Reserved.</div>
</footer>

<!-- booking call to action -->
<section class="cta">
  <div class="hand-l" role="img" aria-label="Gloved hand holding a denture model"></div>
  <div class="hand-r" role="img" aria-label="Gloved hand holding a dental mirror"></div>
  <h2 class="serif">Book your Dental</h2>
  <h3 class="serif">Appointment Today</h3>
  <p>Gap Free Check-Up, Cleaning, X-Rays and Fillings are available<br>for eligible patients with health insurance</p>
  <div class="btn" style="left:278px;top:219px;width:233px;height:41px">
    <svg viewBox="0 0 16 16" fill="none" stroke="#fff" stroke-width="1.5"><rect x="2" y="3" width="12" height="11" rx="1"/><path d="M2 6h12M5 1v4M11 1v4"/></svg>Book an appointment
  </div>
</section>
<div class="leaf"><svg width="40" height="40" viewBox="0 0 24 24" fill="#111"><path d="M12 4c2 2 2 6 0 9-2-3-2-7 0-9zM5 8c3 0 6 2 6.5 6C8 14 5 11 5 8zM19 8c0 3-3 6-6.5 6 .5-4 3.5-6 6.5-6zM8 18c1.5-1 3-1.5 4-1.5s2.5.5 4 1.5"/></svg></div>

</body>
</html>
```